We need a cover designed for our book on parenting. The focus of this book is on the parents, not on the child! We like the idea of this title having a double meaning - insight as in gaining insights into parenting, and "in sight" as in looking inward as parents and how to improve ourselves rather than looking outward to improve our children. We would love for the cover to somehow represent this double meaning. I can upload an excerpt from the book soon over the next few days.

Reason: We are still reviewing the amazing designs! Thank you so much! :)

Target Market(s)

Parents with kids of any age from babies through adult children.

Requirements
Must have
• Title is: Harborlight Parenting
• Subtitle is: Steady Homes, Calmer Hearts Ahead
• Authors names: Lena Marsh, LCSW Oscar Marsh, Ph.D.

```html
<!DOCTYPE html>
<html lang="en">
<head>
<meta charset="utf-8">
<title>Harborlight Parenting – Cover</title>
<link href="https://fonts.googleapis.com/css2?family=Alfa+Slab+One&family=Arvo:wght@700&family=Arimo:wght@400&family=PT+Sans:wght@400&display=swap" rel="stylesheet">
<style>
  :root {
    --bg: #eeeeee;
    --navy-top: #0a4f98;
    --navy-mid: #08367c;
    --navy-deep: #061f5c;
    --title: #cfe6f6;
    --accent: #2db6ea;
    --ink: #ffffff;
    --glow: #1a64c4;
  }
  * { margin: 0; padding: 0; box-sizing: border-box; }
  html, body { width: 1200px; height: 1200px; overflow: hidden; background: var(--bg); }
  .spread {
    position: relative; width: 1200px; height: 1200px;
    display: flex; justify-content: center; align-items: center; gap: 60px;
  }
  .cover {
    position: relative; width: 500px; height: 760px;
    background: linear-gradient(180deg, var(--navy-top) 0%, var(--navy-mid) 55%, var(--navy-deep) 100%);
    color: var(--ink); overflow: hidden;
  }
  .cover--back { background: linear-gradient(180deg, var(--navy-mid) 0%, var(--navy-deep) 100%); }

  .lamp-art { position: absolute; display: block; }
  .front .lamp-art { left: 180px; top: 90px; width: 230px; height: 190px; }

  .title {
    position: absolute; right: 30px; top: 270px; text-align: right;
    font-family: "Alfa Slab One", serif; color: var(--title);
    font-size: 54px; line-height: 1.05; letter-spacing: 0.5px;
  }
  .title span { display: block; }
  .title .line-2 { font-size: 64px; }

  .subtitle {
    position: absolute; right: 30px; top: 460px; text-align: right;
    font-family: "Arvo", serif; font-weight: 700; color: var(--accent);
    font-size: 40px; line-height: 1.12;
  }
  .subtitle span { display: block; }

  .authors {
    position: absolute; left: 0; right: 30px; bottom: 48px; text-align: right;
    font-family: "Arimo", sans-serif; font-size: 21px; color: var(--ink);
  }
  .authors .amp { font-size: 13px; margin: 0 4px; }

  .back .lamp-art { left: 150px; top: 30px; width: 200px; height: 200px; }
  .back-heading {
    position: absolute; left: 0; right: 0; top: 210px; text-align: center;
    font-family: "Arvo", serif; font-weight: 700; color: var(--accent);
    font-size: 34px; line-height: 1.1;
  }
  .blurb {
    position: absolute; left: 40px; right: 40px; top: 310px; text-align: center;
    font-family: "PT Sans", sans-serif; font-size: 19px; line-height: 1.5; color: var(--ink);
  }
</style>
</head>
<body>
<main class="spread">
  <section class="cover front" aria-label="Front cover">
    <svg class="lamp-art" viewBox="0 0 230 190" role="img" aria-label="Illustration of a desk lamp shining a warm light">
      <defs>
        <radialGradient id="lampGlowFront" cx="65%" cy="60%" r="50%">
          <stop offset="0" stop-color="#f4f0b0" stop-opacity="0.9"/>
          <stop offset="0.35" stop-color="#3a7fd0" stop-opacity="0.5"/>
          <stop offset="1" stop-color="#0a4f98" stop-opacity="0"/>
        </radialGradient>
      </defs>
      <rect width="230" height="190" fill="url(#lampGlowFront)"/>
    </svg>
    <h1 class="title"><span class="line-1">HARBORLIGHT</span><span class="line-2">PARENTING</span></h1>
    <p class="subtitle"><span>Steady Homes,</span><span>Calmer Hearts</span><span>Ahead</span></p>
    <p class="authors">Lena Marsh, LCSW<span class="amp">&amp;</span>Oscar Marsh, Ph.D</p>
  </section>

  <section class="cover cover--back back" aria-label="Back cover">
    <svg class="lamp-art" viewBox="0 0 200 200" role="img" aria-label="Small desk lamp illustration within a soft blue glow">
      <defs>
        <radialGradient id="lampGlowBack" cx="50%" cy="50%" r="50%">
          <stop offset="0" stop-color="#f4f0b0" stop-opacity="0.7"/>
          <stop offset="0.25" stop-color="#1a64c4" stop-opacity="0.8"/>
          <stop offset="1" stop-color="#08367c" stop-opacity="0"/>
        </radialGradient>
      </defs>
      <rect width="200" height="200" fill="url(#lampGlowBack)"/>
    </svg>
    <h2 class="back-heading">Steady Homes,<br>Calmer Hearts Ahead</h2>
    <p class="blurb">We need a cover designed for our book on parenting. The focus of this book is on the parents, not on the child! We like the idea of this title having a double meaning - insight as in gaining insights into parenting, and "in sight" as in looking inward as parents and how to improve ourselves rather than looking outward to improve our children. We would love for the cover to somehow represent this double meaning. I can upload an excerpt from the book soon over the next few days.</p>
  </section>
</main>
</body>
</html>
```